International business needs business cards

Our company, DRV Ventures Inc. is in the business of supplying a range construction products with particular emphasis on CEMENT. We have developed our own brand - TORVAN SUPPLIES - with which to infiltrate the market. We are launching our brand of cement (TORVAN Type IS Cement) into the Caribbean which is unlike anything this market has ever seen. A monopoly has existed here for the past 60-odd years and the market has now opened to allow the importation of other brands and consumers are anxious and ready for change/improvement. We are very excited to be launching and want to make a great first impression. We will be conducting workshops and seminars (from government level to the hardware store owners) and we want our business card to give us the strong, confident introduction that we need.

Target Market(s)

construction; builders; engineers; home owners

Industry/Entity Type

Construction

Contact Information for Business Card

Marisol Depree
CEO
cell # 1 555 4180736
Ground floor,Lindell Plaza Suite 2734
George Town,Grand Cayman
Cayman Islands,KY1-4823
EMAIL: m.depree@drvventuresinc.example
web site drvventuresinc.example

COMPANY: skype info drv.ventures.example

second card
Yvette Brannock-Depree
CFO
CELL# 1 555 607 3941
George Town,Grand Cayman
Cayman Islands,KY1-4823
EMAIL: y.brannockdepree@drvventuresinc.example
website drvventuresinc.example

Requirements
Must have
• Business cards must display BOTH logos - DRV is the company and TORVAN is the brand.

```html
<!DOCTYPE html>
<html lang="en">
<head>
<meta charset="utf-8">
<title>DRV Ventures Inc. – Business Card</title>
<link rel="stylesheet" href="https://fonts.googleapis.com/css2?family=Open+Sans:wght@400;600;700&display=swap">
<style>
  :root {
    --bg: #8c8c8c;
    --card-front: #f2f2f2;
    --card-back: #000000;
    --maroon: #6e1116;
    --ink: #1a1a1a;
    --text: #4a4a4a;
    --rule: #c9c9c9;
    --white: #ffffff;
  }
  * { box-sizing: border-box; margin: 0; padding: 0; }
  html, body { width: 1105px; height: 1200px; overflow: hidden; }
  body {
    background: var(--bg);
    font-family: "Open Sans", Arial, sans-serif;
    position: relative;
  }
  .card {
    position: absolute;
    left: 182px;
    width: 748px;
    height: 425px;
    overflow: hidden;
  }
  .card--front { top: 120px; background: var(--card-front); }
  .card--back { top: 637px; background: var(--card-back); }

  /* Front: brand column */
  .brand {
    position: absolute;
    display: flex;
    align-items: center;
    gap: 10px;
  }
  .brand__square {
    background: var(--maroon);
    flex: none;
  }
  .brand__name {
    font-weight: 700;
    color: var(--ink);
    line-height: 1.1;
    white-space: nowrap;
  }
  .brand--company { left: 88px; top: 74px; }
  .brand--company .brand__square { width: 72px; height: 72px; }
  .brand--company .brand__name { font-size: 20px; }
  .brand--product { left: 128px; top: 228px; }
  .brand--product .brand__square { width: 56px; height: 56px; }
  .brand--product .brand__name { font-size: 18px; }

  .divider {
    position: absolute;
    left: 345px;
    top: 80px;
    width: 1px;
    height: 290px;
    background: var(--rule);
  }

  /* Front: contact column */
  .contact {
    position: absolute;
    left: 377px;
    top: 67px;
    color: var(--text);
    white-space: nowrap;
  }
  .contact__name {
    font-size: 27px;
    font-weight: 600;
    color: var(--maroon);
    line-height: 35px;
  }
  .contact__role { font-size: 20px; color: var(--ink); line-height: 25px; }
  .contact__address {
    font-size: 19px;
    line-height: 27px;
    margin-top: 9px;
    font-style: normal;
  }
  .contact__list { list-style: none; margin-top: 6px; }
  .contact__item {
    display: flex;
    align-items: center;
    gap: 12px;
    font-size: 19px;
    line-height: 28px;
  }
  .contact__icon { width: 16px; height: 16px; flex: none; }

  .card__rule {
    position: absolute;
    left: 0; right: 0;
    top: 389px;
    height: 3px;
    background: var(--ink);
  }
  .card__band {
    position: absolute;
    left: 0; right: 0;
    top: 397px;
    bottom: 0;
    background: var(--maroon);
  }

  /* Back */
  .back-mark {
    position: absolute;
    left: 0; right: 0;
    top: 112px;
    display: flex;
    flex-direction: column;
    align-items: center;
    gap: 16px;
  }
  .back-mark__square { width: 130px; height: 130px; background: var(--maroon); }
  .back-mark__name { font-size: 24px; line-height: 33px; font-weight: 700; color: var(--white); }
  .back-url {
    position: absolute;
    left: 0; right: 0;
    top: 368px;
    text-align: center;
    color: var(--white);
    font-size: 19px;
    line-height: 26px;
    letter-spacing: 4px;
  }
</style>
</head>
<body>
  <section class="card card--front" aria-label="Card front">
    <div class="brand brand--company">
      <span class="brand__square"></span>
      <span class="brand__name">DRV<br>Ventures Inc.</span>
    </div>
    <div class="brand brand--product">
      <span class="brand__square"></span>
      <span class="brand__name">TORVAN<br>Supplies</span>
    </div>

    <div class="divider"></div>

    <div class="contact">
      <h1 class="contact__name">Marisol Depree</h1>
      <p class="contact__role">CEO</p>
      <address class="contact__address">
        Ground floor<br>
        Lindell Plaza Suite 2734<br>
        George Town,Grand Cayman<br>
        Cayman Islands,KY1-4823
      </address>
      <ul class="contact__list">
        <li class="contact__item">
          <svg class="contact__icon" viewBox="0 0 16 16"><rect x="3.5" y="0.5" width="9" height="15" rx="1.5" fill="var(--maroon)"/><rect x="5" y="2.5" width="6" height="9" fill="var(--card-front)"/></svg>
          1 555 4180736
        </li>
        <li class="contact__item">
          <svg class="contact__icon" viewBox="0 0 16 16"><rect x="0.5" y="3" width="15" height="10" fill="var(--maroon)"/><path d="M1 3.5 L8 9 L15 3.5" fill="none" stroke="var(--card-front)" stroke-width="1.3"/></svg>
          m.depree@drvventuresinc.example
        </li>
        <li class="contact__item">
          <svg class="contact__icon" viewBox="0 0 16 16"><circle cx="8" cy="8" r="7.5" fill="var(--maroon)"/><path d="M0.5 8 H15.5 M8 0.5 C4 4 4 12 8 15.5 M8 0.5 C12 4 12 12 8 15.5" fill="none" stroke="var(--card-front)" stroke-width="1"/></svg>
          www.drvventuresinc.example
        </li>
      </ul>
    </div>

    <div class="card__rule"></div>
    <div class="card__band"></div>
  </section>

  <section class="card card--back" aria-label="Card back">
    <div class="back-mark">
      <span class="back-mark__square"></span>
      <span class="back-mark__name">DRV Ventures Inc.</span>
    </div>
    <p class="back-url">www.drvventuresinc.example</p>
  </section>
</body>
</html>
```